I need an amazing business card!

I am the principle in my own software company that develops zorPad and mobile applications. I require a great business card design. I've attached my corporate logo (Thanks Tomas!).
I would like the design to integrate the logo, my name, email address and skype account:
name Brent Olafsen
email brentolafsen@tavrik.com
skype brentolafsen.net
I would like the back of the card to have a "write on me area" similar to the "write on me" card on this page, row 6:
http://us.prindlewick.com/design-templates/business-cards/#industry=Computing%20%26%20IT
As far as the rest - it's all you!
Updates
1) Please add an example telephone number as well.
Industry/Entity Type
Software
Look and feel
Each slider illustrates characteristics of the customer's brand and the style your logo design should communicate.

```html
<!DOCTYPE html>
<html lang="en">
<head>
<meta charset="utf-8">
<title>tavrik business card</title>
<link rel="stylesheet" href="https://fonts.googleapis.com/css2?family=Montserrat:wght@500&family=Oswald:wght@500&family=Roboto+Condensed:wght@300;400&display=swap">
<style>
  :root {
    --backdrop: #e9e9e6;
    --green: #a4c34b;
    --green-light: #c3dc52;
    --green-mid: #b1cd4d;
    --green-dark: #95b443;
    --paper: #f2f2f2;
    --white: #ffffff;
  }
  * { box-sizing: border-box; margin: 0; padding: 0; }
  html, body { width: 1200px; height: 896px; overflow: hidden; }
  body {
    background: var(--backdrop);
    position: relative;
    font-family: "Roboto Condensed", sans-serif;
  }
  .card {
    position: absolute;
    left: 240px;
    width: 720px;
    height: 412px;
    overflow: hidden;
    box-shadow: 0 6px 18px rgba(0,0,0,.18);
  }
  .card--front { top: 24px; background: var(--green); }
  .card--back { top: 460px; background: var(--paper); }

  /* front */
  .front__band {
    position: absolute; left: 0; right: 0; top: 296px; height: 116px;
    background: var(--green-mid);
    border-top: 10px solid var(--green-light);
  }
  .front__band::before {
    content: ""; position: absolute; left: 0; right: 0; top: 4px; height: 3px;
    background: var(--green-dark);
  }
  .front__band::after {
    content: ""; position: absolute; left: 0; right: 0; bottom: 18px; height: 2px;
    background: var(--green-light);
  }
  .brand {
    position: absolute;
    display: flex; flex-direction: column; align-items: center; gap: 14px;
  }
  .front__brand { left: 0; right: 0; top: 62px; }
  .brand__square {
    width: 104px; height: 104px; border-radius: 22px; background: var(--white);
  }
  .brand__name {
    font-family: "Montserrat", sans-serif; font-weight: 500;
    font-size: 28px; letter-spacing: 14px; padding-left: 14px;
    color: var(--white);
  }

  /* back */
  .back__brand { left: 0; width: 410px; top: 118px; }
  .back__brand .brand__square { background: var(--green); }
  .back__brand .brand__name { color: var(--green); }
  .back__panel {
    position: absolute; right: 0; top: 0; bottom: 0; width: 310px;
    background: var(--green); color: var(--white);
    padding: 40px 0 0 34px;
  }
  .contact__name {
    font-family: "Oswald", sans-serif; font-weight: 500;
    font-size: 34px; line-height: 1; letter-spacing: 1px; text-transform: uppercase;
  }
  .contact__title {
    font-size: 13px; letter-spacing: 1.5px; text-transform: uppercase; margin-top: 4px;
  }
  .contact__address {
    font-size: 17px; font-weight: 300; line-height: 1.4; margin-top: 38px;
  }
  .contact__list { list-style: none; margin-top: 22px; }
  .contact__item {
    display: flex; align-items: center; gap: 12px;
    font-size: 14px; font-weight: 300; height: 27px;
  }
  .contact__icon { width: 16px; height: 16px; flex: none; }
</style>
</head>
<body>

<section class="card card--front">
  <div class="front__band"></div>
  <div class="brand front__brand">
    <div class="brand__square"></div>
    <div class="brand__name">tavrik</div>
  </div>
</section>

<section class="card card--back">
  <div class="brand back__brand">
    <div class="brand__square"></div>
    <div class="brand__name">tavrik</div>
  </div>
  <div class="back__panel">
    <h1 class="contact__name">Brent Olafsen</h1>
    <p class="contact__title">General Manager</p>
    <p class="contact__address">041 12th floor Hale,<br>Corven Road NLB</p>
    <ul class="contact__list">
      <li class="contact__item">
        <svg class="contact__icon" viewBox="0 0 16 16"><rect width="16" height="16" rx="2" fill="#fff"/><path d="M4.5 3.5l2 2-1 1.2c.7 1.5 1.8 2.6 3.3 3.3l1.2-1 2 2-1.2 1.5C7 12 4 9 3 4.7z" fill="#a4c34b"/></svg>
        <span>014 372 5816</span>
      </li>
      <li class="contact__item">
        <svg class="contact__icon" viewBox="0 0 16 16"><rect width="16" height="16" rx="2" fill="#fff"/><rect x="5" y="2.5" width="6" height="11" rx="1" fill="#a4c34b"/><rect x="6" y="4" width="4" height="6.5" fill="#fff"/></svg>
        <span>014 372 5816</span>
      </li>
      <li class="contact__item">
        <svg class="contact__icon" viewBox="0 0 16 16"><rect width="16" height="16" rx="2" fill="#fff"/><rect x="3" y="4.5" width="10" height="7" fill="#a4c34b"/><path d="M3 4.5l5 4 5-4" fill="none" stroke="#fff" stroke-width="1"/></svg>
        <span>brentolafsen@tavrik.com</span>
      </li>
      <li class="contact__item">
        <svg class="contact__icon" viewBox="0 0 16 16"><rect width="16" height="16" rx="2" fill="#fff"/><circle cx="8" cy="8" r="4.8" fill="none" stroke="#a4c34b" stroke-width="1.2"/><ellipse cx="8" cy="8" rx="2" ry="4.8" fill="none" stroke="#a4c34b" stroke-width="1"/><path d="M3.2 8h9.6" stroke="#a4c34b" stroke-width="1"/></svg>
        <span>brentolafsen.net</span>
      </li>
    </ul>
  </div>
</section>

</body>
</html>
```